KRT Flyer to attract applicants 11x17

Lantern Stagehand Collective provides crew for local concerts, filming, theater, and corporate events.
The flyer will be posted on bulletin boards at colleges with theater programs.
Our primary venues are historic theaters in downtown LA
Need a 11x17 poster to attract potential applicants/crew
I have attached a poster that one of our staff made that has all if the relevant info - but i know the poster can look much better than that. I have also attached many images and our logo. It is not necessary to use all of the images, or any of them. The two images of the theater interiors are the venues we operate so they would be the first to include. I can send additional info or images upon request. Thank you

Industry/Entity Type

Entertainment

Requirements
Must have
• APPLY@KRTCREW.EXAMPLE

```html
<!DOCTYPE html>
<html lang="en">
<head>
<meta charset="utf-8">
<title>Lantern Stagehand Collective — Open Position</title>
<link rel="stylesheet" href="https://fonts.googleapis.com/css2?family=Bebas+Neue&family=Great+Vibes&family=Poppins:wght@300;400;600&display=swap">
<style>
  :root {
    --sky: #d6edf9;
    --band: #2d56a8;
    --white: #ffffff;
    --venue-violet: #4a2a6e;
    --venue-plum: #7a3a5c;
    --venue-amber: #b8743a;
    --venue-gold: #d49a55;
  }
  html, body {
    margin: 0;
    padding: 0;
    width: 1200px;
    height: 777px;
    overflow: hidden;
    background: var(--sky);
  }
  .flyer {
    position: relative;
    width: 1200px;
    height: 777px;
    background: var(--sky);
    font-family: "Poppins", sans-serif;
    color: var(--white);
  }
  .venue-photo {
    position: absolute;
    left: 51px;
    top: 33px;
    width: 1098px;
    height: 610px;
    background:
      radial-gradient(ellipse 30% 25% at 30% 12%, rgba(230, 200, 240, 0.55), transparent 70%),
      linear-gradient(180deg, rgba(40, 20, 60, 0.25), rgba(30, 15, 50, 0.35)),
      linear-gradient(90deg, var(--venue-violet) 0%, var(--venue-plum) 30%, var(--venue-amber) 62%, var(--venue-gold) 85%, var(--venue-amber) 100%);
  }
  .brand {
    position: absolute;
    left: 0;
    width: 1200px;
    text-align: center;
  }
  .brand-mark {
    position: absolute;
    left: 584px;
    top: 70px;
    width: 72px;
    height: 72px;
    border: 6px solid var(--white);
    border-radius: 50%;
    box-sizing: border-box;
  }
  .brand-name {
    top: 188px;
    font-weight: 600;
    font-size: 25px;
    letter-spacing: 1px;
  }
  .headline-script {
    position: absolute;
    left: 0;
    width: 1240px;
    top: 262px;
    text-align: center;
    font-family: "Great Vibes", cursive;
    font-size: 118px;
    line-height: 1;
  }
  .headline-block {
    position: absolute;
    left: 0;
    width: 1240px;
    top: 358px;
    text-align: center;
    font-family: "Bebas Neue", sans-serif;
    font-size: 178px;
    line-height: 1;
    letter-spacing: -2px;
  }
  .divider {
    position: absolute;
    left: 479px;
    top: 524px;
    width: 282px;
    height: 1px;
    background: var(--white);
  }
  .pitch {
    position: absolute;
    left: 0;
    width: 1240px;
    top: 535px;
    margin: 0;
    text-align: center;
    font-size: 23px;
    line-height: 29px;
    font-weight: 400;
  }
  .contact-band {
    position: absolute;
    left: 51px;
    top: 643px;
    width: 1098px;
    height: 101px;
    background: var(--band);
  }
  .apply-label {
    position: absolute;
    left: 55px;
    top: 12px;
    font-family: "Bebas Neue", sans-serif;
    font-size: 48px;
    line-height: 1;
  }
  .apply-email {
    position: absolute;
    left: 51px;
    top: 56px;
    font-weight: 300;
    font-size: 24px;
    line-height: 1;
  }
  .website {
    position: absolute;
    right: 40px;
    top: 30px;
    font-weight: 400;
    font-size: 36px;
    line-height: 1;
    letter-spacing: 1px;
  }
</style>
</head>
<body>
<main class="flyer">
  <div class="venue-photo" role="img" aria-label="Interiors of two ornate historic downtown Los Angeles theaters: a domed auditorium with carved proscenium on the left and a gilded balcony hall on the right"></div>

  <div class="brand-mark"></div>
  <div class="brand brand-name">LANTERN STAGEHAND COLLECTIVE</div>

  <div class="headline-script">Has Open</div>
  <div class="headline-block">POSITION</div>

  <div class="divider"></div>
  <p class="pitch">We are looking for talented Technicians<br>to add to our Roster of skilled professionals.</p>

  <section class="contact-band">
    <div class="apply-label">SEND RESUME TO:</div>
    <div class="apply-email">APPLY@KRTCREW.EXAMPLE</div>
    <div class="website">WWW.KRTCREW.EXAMPLE</div>
  </section>
</main>
</body>
</html>
```